Chimney Service company needs new business card design

We need a updated business card with our new logo added. We provide a full range of chimney services throughout Vermont and New Hampshire. The business card will be one sided and color. Attached is our current business card another document showing all the information we would like on the card.
We dont like a lot of flashy colors.... here is a link to our website to get an idea of our branding www.flueguardianvt.example

Target Market(s)

homeowners

Industry/Entity Type

Business

Contact Information for Business Card

See attached sheet for content.

Font styles to use
Serif
Sans Serif

Requirements
Must have
• all information provided on separate sheet
Should not have
• Additional information that may clogg up design

```html
<!DOCTYPE html>
<html lang="en">
<head>
<meta charset="utf-8">
<title>Flue Guardian Business Card</title>
<link href="https://fonts.googleapis.com/css2?family=Cinzel:wght@400;700&display=swap" rel="stylesheet">
<style>
:root{
  --bg:#e6e6e6;
  --card:#ffffff;
  --ink:#2b2b2b;
  --band:#3a3a3a;
  --red:#a10d0d;
  --rule:#555555;
  --light:#f2f2f2;
}
*{margin:0;padding:0;box-sizing:border-box}
html,body{width:1200px;height:1000px;overflow:hidden;background:var(--bg)}
.card{
  position:absolute;left:100px;top:215px;width:1000px;height:571px;
  background:var(--card);border-radius:34px;overflow:hidden;
  font-family:"Cinzel",serif;color:var(--ink);
  box-shadow:0 10px 30px rgba(0,0,0,.18);
}
.shapes{position:absolute;inset:0}
.brand{position:absolute;left:58px;top:62px;display:flex;align-items:center;gap:22px}
.brand-mark{width:82px;height:82px;background:var(--ink)}
.brand-name{font-size:44px;font-weight:400;letter-spacing:1px;line-height:1;
  padding-bottom:10px;border-bottom:2px solid var(--ink)}
.tagline{position:absolute;left:60px;top:160px;font-size:15px;letter-spacing:.5px}
.divider{position:absolute;left:640px;top:44px;width:1.5px;height:130px;background:var(--rule)}
.perks{position:absolute;left:662px;top:54px;list-style:none;color:var(--red);font-size:19px;line-height:33px}
.services{position:absolute;left:112px;top:212px;width:766px;text-align:center;color:var(--light)}
.services h2{font-size:22px;font-weight:700;letter-spacing:.5px;margin-bottom:10px}
.services p{font-size:23px;line-height:36px}
.contact{position:absolute;left:0;right:0;top:408px;text-align:center;font-size:24px;line-height:40px}
.contact .row{display:flex;justify-content:center;align-items:center;gap:12px}
.contact svg{width:22px;height:22px;fill:var(--red)}
.sep{color:var(--rule)}
.web .domain{color:var(--red);font-weight:700}
</style>
</head>
<body>
<div class="card">
  <svg class="shapes" width="1000" height="571" viewBox="0 0 1000 571" aria-hidden="true">
    <rect class="service-band" x="112" y="200" width="766" height="178" fill="var(--band)"/>
    <rect class="accent-right" x="885" y="182" width="115" height="96" fill="var(--red)"/>
    <rect class="accent-left" x="0" y="300" width="105" height="100" fill="var(--red)"/>
  </svg>

  <div class="brand">
    <div class="brand-mark"></div>
    <div class="brand-name">Flue Guardian</div>
  </div>
  <div class="tagline">Serving VT and New Hampshire since 1989</div>

  <div class="divider"></div>
  <ul class="perks">
    <li>Fully Insured</li>
    <li>Free Estimates</li>
    <li>Family owned and operated</li>
  </ul>

  <section class="services">
    <h2>Services We Provide</h2>
    <p>Full Masonry Services | Historic chimney restoration |</p>
    <p>Stainless steel liners | New Chimney Installations |</p>
    <p>Fully Certified Chimney Sweeps</p>
  </section>

  <div class="contact">
    <div class="row">
      <svg viewBox="0 0 24 24" aria-hidden="true"><path d="M6.6 10.8a15.1 15.1 0 0 0 6.6 6.6l2.2-2.2a1 1 0 0 1 1-.25 11.4 11.4 0 0 0 3.6.57 1 1 0 0 1 1 1V20a1 1 0 0 1-1 1A17 17 0 0 1 3 4a1 1 0 0 1 1-1h3.5a1 1 0 0 1 1 1c0 1.25.2 2.45.57 3.57a1 1 0 0 1-.25 1z"/></svg>
      <span>802-555-0147</span>
      <span class="sep">|</span>
      <svg viewBox="0 0 24 24" aria-hidden="true"><path d="M3 5h18a1 1 0 0 1 1 1v12a1 1 0 0 1-1 1H3a1 1 0 0 1-1-1V6a1 1 0 0 1 1-1zm1 2.2V17h16V7.2l-8 5.3z M4.6 7 12 11.9 19.4 7z"/></svg>
      <span>info@flueguardianvt.example</span>
    </div>
    <div class="web">www.<span class="domain">flueguardianvt</span>.example</div>
  </div>
</div>
</body>
</html>
```